Wordpress - For IT, Cloud/Hosting, Residential/Commercial Construction Services

We are a holding company for service companies. We want the current Wordpress site modified or a new wordpress site completed. We want this site to be the parent website, that then has pull down menus linking to our other website (currently http://brightwallfix.com, http://q7v.host and would like it to be easy and fluid as we acquire more companies as we have with TKLS, Inc., B&J Construction, Brightwall Fix etc. Model after sites like Pemrose.com, Tallowbine.com, QDV.com,.vanterelm.com

------

The parent is the main site q7v Corp. Below that are sub corps and DBAs. q7v Corp stands for Quick 7 Venture Corp. q7v Offers IT manages services, 24x7 support, Monitoring NOC, Remote Hands, Onsite support services. We have acquired TKLS, Inc, B & J Construction, BrightwallFix.com. We plan to acquire/spin up many companies that offer service, support and installation offerings and will all be known as an q7v Corp Company for branding purposes. We recently had our logo done, but then ran it through 3d glass as we like the look better than the original works. We have original files in vector, but not the 3D galss door render.

Target Market(s)

IT Server and Desktop Support. Construction. Mold Remediation. Mergers and Acquisitions.

Industry/Entity Type

It Company

Coding

Coded - Design and coding required

Font styles to use
Sans Serif

Colors
0792cd

Requirements
Must have
• Clean interface. Modern design. Mobile device and multi browser support. Must be for Wordpress. Job posting with resume submission module.Hook to our Web hosting portal (Tormund) API into VexaLine Reseller portal, customer portal to allow payments to their account etc.. Easy to edit. Easy to add to, Press Release Section, Investor Relations etc.
Should not have
• Slow loading. Played out design. Over use of stock images. Copied from a competitor or something point to such.

```html
<!DOCTYPE html>
<html lang="en">
<head>
<meta charset="utf-8">
<title>Q7V Corp</title>
<link rel="stylesheet" href="https://fonts.googleapis.com/css2?family=Poppins:wght@300;400;500;600&family=Open+Sans:wght@400;600;700&display=swap">
<style>
:root{
  --brand:#0792cd;
  --brand-deep:#1566b0;
  --nav-active:#1a70b8;
  --ink:#222;
  --body:#555;
  --muted:#777;
  --line:#dcdcdc;
  --navy:#0d1e33;
  --panel:#1b7fc8;
  --tile:rgba(23,108,178,.92);
  --white:#fff;
}
*{box-sizing:border-box;margin:0;padding:0}
html,body{width:1200px;height:3136px;overflow:hidden;background:var(--white)}
body{position:relative;font-family:"Open Sans",Arial,sans-serif;color:var(--ink)}
.abs{position:absolute}
a{color:inherit;text-decoration:none}

/* header */
.site-header{left:0;top:0;width:1200px;height:88px;border-top:4px solid var(--nav-active);background:var(--white);box-shadow:0 1px 3px rgba(0,0,0,.08);z-index:2}
.brand{left:115px;top:16px;font-family:"Poppins",sans-serif;font-weight:600;color:var(--brand-deep);line-height:1;text-align:center}
.brand .name{font-size:30px;letter-spacing:1px;display:block}
.brand .sub{font-size:12px;letter-spacing:9px;display:block;margin-top:2px;padding-left:8px}
.main-nav{left:387px;top:0;height:84px;display:flex;font-size:16px;color:#333}
.main-nav a{display:flex;align-items:center;padding:0 23px;height:84px}
.main-nav a.active{background:var(--nav-active);color:var(--white)}
.main-nav svg{margin-left:5px}

/* hero */
.hero{left:0;top:88px;width:1200px;height:514px;background:linear-gradient(120deg,#0b2a4a 0%,#174a7a 40%,#2a6aa6 70%,#153e68 100%)}
.hero-title{left:0;top:190px;width:1200px;text-align:center;font-family:"Poppins",sans-serif;font-weight:600;font-size:108px;color:var(--white);letter-spacing:3px}
.hero-down{left:574px;top:510px;width:52px;height:52px}

/* section titles */
.section-title{left:0;width:1200px;text-align:center;font-family:"Poppins",sans-serif;font-weight:400;font-size:44px;color:var(--ink)}

/* provide cards */
.provide-card{top:767px;width:233px}
.provide-card .photo{width:233px;height:165px}
.provide-card h3{font-family:"Poppins",sans-serif;font-weight:500;font-size:17px;margin-top:20px;line-height:29px;color:var(--ink)}
.provide-card p{font-size:14px;color:var(--body);margin-top:2px}
.provide-card .more{display:block;font-size:14px;color:var(--brand);margin-top:16px}

/* what we do */
.wwd-back{left:94px;top:1175px;width:466px;height:307px;background:var(--brand-deep)}
.wwd-photo{left:111px;top:1156px;width:468px;height:310px;background:linear-gradient(135deg,#6f8aa0 0%,#b9b37a 45%,#d8c25a 60%,#8a9aa4 100%);box-shadow:0 4px 18px rgba(0,0,0,.2)}
.wwd-title{left:619px;top:1145px;font-family:"Poppins",sans-serif;font-size:44px;font-weight:400}
.wwd-text{left:619px;top:1226px;width:470px;font-size:14.5px;line-height:30px;color:#444}
.btn{display:inline-flex;align-items:center;justify-content:center;background:var(--brand-deep);color:var(--white);font-family:"Poppins",sans-serif;font-weight:500;font-size:15px}
.wwd-btn{left:621px;top:1442px;width:137px;height:42px}

/* blog */
.blog-card{top:1660px;width:315px;height:414px;border:1px solid var(--line);background:var(--white)}
.blog-card .photo{position:relative;width:313px;height:198px}
.blog-card .tag{position:absolute;left:0;bottom:0;width:115px;height:28px;background:var(--brand-deep);color:var(--white);font-size:14px;font-weight:600;display:flex;align-items:center;justify-content:center}
.blog-card h3{font-family:"Poppins",sans-serif;font-weight:500;font-size:17.5px;line-height:29px;margin:20px 22px 0;color:var(--ink)}
.blog-card p{font-size:14px;line-height:30px;color:var(--muted);margin:14px 22px 0}
.blog-card p a{color:var(--brand);text-decoration:underline}

/* help band */
.help-band{left:0;top:2168px;width:1200px;height:408px;background:linear-gradient(110deg,#07121f 0%,#132a44 40%,#0c1c30 70%,#1b3a58 100%)}
.tile{width:161px;height:138px;background:var(--tile);color:var(--white);font-size:15px;text-align:center;display:flex;flex-direction:column;align-items:center;justify-content:flex-end;padding-bottom:16px}
.tile svg{margin-bottom:12px}
.help-panel{left:456px;top:2231px;width:631px;height:286px;background:var(--panel);color:var(--white);padding:36px 53px}
.help-panel h2{font-family:"Poppins",sans-serif;font-weight:300;font-size:33px}
.help-panel p{font-size:14.5px;line-height:24px;margin-top:14px;width:440px}
.help-input{margin-top:16px;width:544px;height:46px;background:var(--white);color:#888;font-size:13px;display:flex;align-items:center;padding-left:20px}
.help-send{display:inline-block;margin-top:16px;font-weight:700;font-size:14px;text-decoration:underline}

/* footer */
.footer-brand{left:0;top:2640px;width:1200px;text-align:center;font-family:"Poppins",sans-serif;font-weight:600;color:var(--brand-deep);line-height:1}
.footer-brand .name{font-size:40px;letter-spacing:1px;display:block}
.footer-brand .sub{font-size:14px;letter-spacing:12px;display:block;margin-top:2px;padding-left:12px}
.social{top:2740px;width:40px;height:40px;border:2px solid var(--brand-deep);border-radius:50%}
.foot-col{top:2806px}
.foot-col h4{font-family:"Poppins",sans-serif;font-weight:400;font-size:19px;color:#333;margin-bottom:22px}
.foot-col li{list-style:none;font-size:13px;color:#444;line-height:28.5px}
.field{height:38px;border:1px solid #9a9a9a;font-size:12px;color:#888;padding:0 16px;display:flex;align-items:center}
.send-btn{left:669px;top:3010px;width:77px;height:28px;font-size:14px}
.copyright{left:0;top:3094px;width:1200px;text-align:center;font-size:13px;color:#444}
</style>
</head>
<body>

<header class="site-header abs">
  <div class="brand abs"><span class="name">Q7V</span><span class="sub">CORP</span></div>
  <nav class="main-nav abs">
    <a class="active">Home</a><a>About Us</a><a>Solutions</a><a>Support</a><a>Partners</a><a>Blog</a>
    <a>Companies<svg width="10" height="7" viewBox="0 0 10 7"><path d="M1 1l4 4 4-4" fill="none" stroke="#333" stroke-width="1.6"/></svg></a>
  </nav>
</header>

<section class="hero abs" role="img" aria-label="Two engineers with a laptop in a server room, overlaid with blue cloud network graphics"></section>
<h1 class="hero-title abs">Q7V CORP</h1>
<svg class="hero-down abs" viewBox="0 0 52 52"><circle cx="26" cy="26" r="24" fill="none" stroke="#fff" stroke-width="2"/><path d="M26 14v22M18 28l8 8 8-8" fill="none" stroke="#fff" stroke-width="2"/></svg>

<h2 class="section-title abs" style="top:682px">We Provide</h2>

<article class="provide-card abs" style="left:111px">
  <div class="photo" role="img" aria-label="Technician working at a server rack" style="background:linear-gradient(135deg,#3a3f46,#8a6a5c 55%,#2b3038)"></div>
  <h3>Services in IT</h3><p>Lorem ipsum dolor sit amet</p><a class="more">Read More »</a>
</article>
<article class="provide-card abs" style="left:360px">
  <div class="photo" role="img" aria-label="Laptop showing cloud storage beside a coffee cup" style="background:linear-gradient(135deg,#c9ced3,#6f7b86 55%,#e2e4e6)"></div>
  <h3>Cloud/Hosting</h3><p>Lorem ipsum dolor sit amet</p><a class="more">Read More »</a>
</article>
<article class="provide-card abs" style="left:606px">
  <div class="photo" role="img" aria-label="Carpenter building a wooden roof frame" style="background:linear-gradient(135deg,#4a3626,#b07a4a 55%,#3c2a1e)"></div>
  <h3>Home/Commercial<br>Services</h3><p>Lorem ipsum dolor sit amet</p><a class="more">Read More »</a>
</article>
<article class="provide-card abs" style="left:855px">
  <div class="photo" role="img" aria-label="Two workers in safety vests inside an empty warehouse" style="background:linear-gradient(180deg,#9fb3c4,#d6dde3 60%,#a9b2b8)"></div>
  <h3>Construction Services</h3><p>Lorem ipsum dolor sit amet</p><a class="more">Read More »</a>
</article>

<div class="wwd-back abs"></div>
<div class="wwd-photo abs" role="img" aria-label="Engineer in a hard hat reviewing a tablet with a colleague at an industrial site"></div>
<h2 class="wwd-title abs">What We Do</h2>
<p class="wwd-text abs">q7v Corp is a Corvane and Tallowbine IT Solution Provider. We provide support for Desktops, Laptops, Tablets, Mobile Devices,Networking, WiFi, Server, Design and more by providing Remote and OnSite Support Services. q7v Corp (Quick 7 Venture) Full service one stop shop service provider. Our CEO and Founder Dale Ferrin has been working with Tallowbine Solutions all the way back to...</p>
<a class="btn wwd-btn abs">Read More</a>

<h2 class="section-title abs" style="top:1564px">Service Blog</h2>

<article class="blog-card abs" style="left:111px">
  <div class="photo" role="img" aria-label="Hands working on a tablet and laptop over charts" style="background:linear-gradient(135deg,#8a98a6,#dfe3e6 50%,#5b6670)"><span class="tag">Q7V Corp</span></div>
  <h3>Lorem ipsum dolor sit amet, consectetur adipiscing</h3>
  <p>Sed ut perspiciatis unde omnis iste natus error sit voluptatem accusantium eaque ipsa quae ab illo inventore...<a>Read More</a></p>
</article>
<article class="blog-card abs" style="left:441px">
  <div class="photo" role="img" aria-label="Smartphone showing a map app in a city street" style="background:linear-gradient(135deg,#b9a48a,#e8e2d8 50%,#6e7e70)"><span class="tag">Q7V Corp</span></div>
  <h3>Lorem ipsum dolor sit amet, consectetur adipiscing</h3>
  <p>Sed ut perspiciatis unde omnis iste natus error sit voluptatem accusantium eaque ipsa quae ab illo inventore...<a>Read More</a></p>
</article>
<article class="blog-card abs" style="left:773px">
  <div class="photo" role="img" aria-label="Technician standing between data center server racks" style="background:linear-gradient(135deg,#22272c,#7c8690 50%,#1b1f24)"><span class="tag">Q7V Corp</span></div>
  <h3>Lorem ipsum dolor sit amet, consectetur adipiscing</h3>
  <p>Sed ut perspiciatis unde omnis iste natus error sit voluptatem accusantium eaque ipsa quae ab illo inventore...<a>Read More</a></p>
</article>

<section class="help-band abs" role="img" aria-label="Dark blue technology background with glowing network lines"></section>
<div class="tile abs" style="left:111px;top:2231px">
  <svg width="52" height="52" viewBox="0 0 52 52" fill="none" stroke="#fff" stroke-width="2"><circle cx="26" cy="22" r="8"/><circle cx="26" cy="22" r="15" stroke-dasharray="5 4"/><path d="M10 44c5-4 10-5 16-5s11 1 16 5"/></svg>IT Services</div>
<div class="tile abs" style="left:282px;top:2231px">
  <svg width="52" height="52" viewBox="0 0 52 52" fill="none" stroke="#fff" stroke-width="2"><path d="M10 28a16 16 0 0 1 32 0"/><rect x="6" y="27" width="8" height="12" rx="3"/><rect x="38" y="27" width="8" height="12" rx="3"/><text x="26" y="34" fill="#fff" stroke="none" font-size="12" font-family="Open Sans,sans-serif" text-anchor="middle">24</text></svg>Support</div>
<div class="tile abs" style="left:111px;top:2379px">
  <svg width="52" height="52" viewBox="0 0 52 52" fill="none" stroke="#fff" stroke-width="2"><rect x="8" y="16" width="36" height="26"/><path d="M8 16l18 14 18-14"/><path d="M16 10h20"/></svg>Email Services</div>
<div class="tile abs" style="left:282px;top:2379px">
  <svg width="52" height="52" viewBox="0 0 52 52" fill="none" stroke="#fff" stroke-width="2"><path d="M14 8l7 9-4 5c2 5 6 9 11 11l5-4 9 7-4 6C24 42 10 28 8 12z"/></svg>+ 125 604 317</div>
<div class="help-panel abs">
  <h2>How can we help?</h2>
  <p>Sed ut perspiciatis unde omnis iste natus error sit voluptatem accusantium doloremque laudantium,</p>
  <div class="help-input">Enter Your Email Address</div>
  <a class="help-send">SEND</a>
</div>

<div class="footer-brand abs"><span class="name">Q7V</span><span class="sub">CORP</span></div>
<span class="social abs" style="left:471px" aria-label="Social link"></span>
<span class="social abs" style="left:526px" aria-label="Social link"></span>
<span class="social abs" style="left:580px" aria-label="Social link"></span>
<span class="social abs" style="left:634px" aria-label="Social link"></span>
<span class="social abs" style="left:689px" aria-label="Social link"></span>

<div class="foot-col abs" style="left:111px"><h4>Companies</h4><ul><li>q7v.host</li><li>Brightwallfix</li><li>TKLS, Inc.</li><li>B&amp;J Construction</li></ul></div>
<div class="foot-col abs" style="left:297px"><h4>Navigation</h4><ul><li>Home</li><li>About Us</li><li>Solutions</li><li>Support</li><li>Partners</li><li>Blog</li></ul></div>
<div class="foot-col abs" style="left:472px"><h4>Other Links</h4><ul><li>Faq</li><li>Privacy Policy</li><li>Terms &amp; Use</li><li>Sitemap</li><li>Contact Us</li></ul></div>
<div class="foot-col abs" style="left:669px"><h4>Get In Touch</h4></div>
<div class="field abs" style="left:669px;top:2866px;width:205px">First Name</div>
<div class="field abs" style="left:882px;top:2866px;width:205px">Last name</div>
<div class="field abs" style="left:669px;top:2912px;width:205px">Email Address</div>
<div class="field abs" style="left:882px;top:2912px;width:205px">Phone No.</div>
<div class="field abs" style="left:669px;top:2958px;width:418px;height:44px;align-items:flex-start;padding-top:6px">Message</div>
<a class="btn send-btn abs">Send</a>

<p class="copyright abs">copyright 2018 &nbsp;|Q7V Corp.All Rights Reserved.</p>

</body>
</html>
```